Business card for marketing analytics company

Need a business card for new company. I have a logo already that I want to be built into the card and should use those colours

Company is called steered by tallies
Design must bring steered by tallies to life not be a card that could be for anyone with a logo put on it.

Like the front to be fairly clean and uncluttered bringing the logo out with a suitable design on the back of the card.

The logo represents a compass and business growth so those themes along with numbers, analytics , data are appropriate.
I'm often working with creative industries so also needs to reflect the creative side of analytics rather than be very corporate looking.

Target Market(s)

Ad agency, media agency, consumer goods clients

Industry/Entity Type

Market Research

Contact Information for Business Card

Needs to include name, title, email and phone number

Colors
f78f20
f68d4d
ec1f27

Requirements
Must have
• Must bring steered by tallies to life not be a card that could be for anyone with a logo put on it.
• Logo, Correct colours
• Like a design on the back that relates to company name
• Designs for both sides
Should not have
• Please do not just submit logo and a coloured card.
• It needs to have a design element to it
• No black background
• No clear cards - needs front & back

```html
<!DOCTYPE html>
<html lang="en">
<head>
<meta charset="utf-8">
<title>Corvale Insight – Business Card</title>
<link href="https://fonts.googleapis.com/css2?family=Roboto:wght@400;500;700&display=swap" rel="stylesheet">
<style>
  :root {
    --backdrop: #e6e6e6;
    --card: #f7f7f7;
    --ink: #3d4a52;
    --ink-soft: #4a4a4a;
    --brand-red: #a3241f;
    --brand-orange: #e8731c;
    --faint: #f1e6df;
  }
  * { margin: 0; padding: 0; box-sizing: border-box; }
  html, body {
    width: 1200px; height: 576px; overflow: hidden;
    background: var(--backdrop);
    font-family: "Roboto", Arial, sans-serif;
  }
  .canvas { position: relative; width: 1200px; height: 576px; }
  .card {
    position: absolute;
    background: var(--card);
    border-radius: 12px;
    overflow: hidden;
  }
  .card--front { left: 82px; top: 138px; width: 484px; height: 294px; }
  .card--back  { left: 602px; top: 138px; width: 480px; height: 291px; }

  .brand { position: absolute; display: flex; align-items: center; }
  .brand__dot {
    border-radius: 50%;
    border: 3px solid var(--brand-orange);
    flex: none;
  }
  .brand__name {
    color: var(--ink);
    font-weight: 500;
    line-height: 1.0;
    white-space: nowrap;
  }
  .card--front .brand { left: 100px; top: 98px; gap: 18px; }
  .card--front .brand__dot { width: 92px; height: 92px; }
  .card--front .brand__name { font-size: 30px; }

  .card--back .brand { left: 258px; top: 30px; gap: 12px; }
  .card--back .brand__dot { width: 66px; height: 66px; border-width: 2px; }
  .card--back .brand__name { font-size: 20px; }

  .edge-band {
    position: absolute; left: 0; top: 0; bottom: 0; width: 42px;
    background: var(--brand-red);
    border-right: 5px solid var(--brand-orange);
  }
  .faint-ring {
    position: absolute; left: 262px; top: 40px;
    width: 224px; height: 224px;
    border-radius: 50%;
    border: 5px solid var(--faint);
  }

  .person { position: absolute; left: 65px; top: 172px; }
  .person__name { color: var(--brand-red); font-weight: 700; font-size: 18px; }
  .person__title { color: var(--ink-soft); font-size: 11px; margin-top: 4px; }

  .contact { position: absolute; left: 66px; top: 222px; list-style: none; }
  .contact__item {
    display: flex; align-items: center; gap: 12px;
    color: var(--ink-soft); font-size: 12px; height: 17px;
  }
  .contact__icon { width: 11px; height: 11px; flex: none; }
</style>
</head>
<body>
<div class="canvas">

  <section class="card card--front" aria-label="Card front">
    <div class="brand">
      <span class="brand__dot"></span>
      <span class="brand__name">Corvale<br>Insight</span>
    </div>
  </section>

  <section class="card card--back" aria-label="Card back">
    <div class="faint-ring"></div>
    <div class="edge-band"></div>
    <div class="brand">
      <span class="brand__dot"></span>
      <span class="brand__name">Corvale<br>Insight</span>
    </div>

    <div class="person">
      <p class="person__name">Mark T. Ellison</p>
      <p class="person__title">Managing Director</p>
    </div>

    <ul class="contact">
      <li class="contact__item">
        <svg class="contact__icon" viewBox="0 0 12 12" aria-hidden="true">
          <path d="M1 4 Q6 0 11 4 L9 5 L8 4 L4 4 L3 5 Z" fill="var(--brand-orange)"/>
          <rect x="2" y="6" width="8" height="5" rx="1" fill="var(--brand-orange)"/>
        </svg>
        1300 418 902
      </li>
      <li class="contact__item">
        <svg class="contact__icon" viewBox="0 0 12 12" aria-hidden="true">
          <circle cx="6" cy="6" r="5" fill="var(--brand-orange)"/>
          <path d="M1 6 H11 M6 1 Q3 6 6 11 M6 1 Q9 6 6 11" stroke="#fff" stroke-width="0.8" fill="none"/>
        </svg>
        www.brightsamplesite.com
      </li>
      <li class="contact__item">
        <svg class="contact__icon" viewBox="0 0 12 12" aria-hidden="true">
          <rect x="0.5" y="2.5" width="11" height="7" fill="var(--brand-orange)"/>
          <path d="M0.5 2.5 L6 7 L11.5 2.5" stroke="#fff" stroke-width="0.9" fill="none"/>
        </svg>
        mark.ellison@brightsamplesite.com
      </li>
    </ul>
  </section>

</div>
</body>
</html>
```